Redgum Ridge Towing website

We need a website design for a towing company based in Australia.
The design should be simple and minimalist. The site can be in colours of the logo are Blue, Red and White (see attached) - but we'd like to see options in some sort of industrial looking metallic theme if possible.
We base our business on our friendly and efficient customer service, the design should attempt to convey this in some way.

```html
<!DOCTYPE html>
<html lang="en">
<head>
<meta charset="utf-8">
<title>Redgum Ridge Towing</title>
<link href="https://fonts.googleapis.com/css2?family=Open+Sans:wght@400;600&display=swap" rel="stylesheet">
<style>
:root{
  --page-dark:#2a2a2a;
  --metal-light:#e4e4e4;
  --metal-mid:#bdbdbd;
  --metal-dark:#8f8f8f;
  --red:#c4161c;
  --blue:#2a5db0;
  --text:#333;
  --muted:#555;
  --footer-link:#5a5a5a;
  --bar:#1d1d1d;
}
*{margin:0;padding:0;box-sizing:border-box}
html,body{width:914px;height:1200px;overflow:hidden}
body{font-family:"Open Sans",Arial,sans-serif;color:var(--text);
  background:radial-gradient(circle,#3a3a3a 1px,transparent 1.2px) 0 0/4px 4px,var(--page-dark);
  position:relative}
.site{position:absolute;left:55px;top:0;width:804px;height:1200px;background:#fff}
.abs{position:absolute}
.metal{background:linear-gradient(115deg,var(--metal-dark) 0%,var(--metal-mid) 25%,var(--metal-light) 45%,#f4f4f4 52%,var(--metal-mid) 70%,var(--metal-dark) 100%)}
/* header */
.header{left:0;top:0;width:804px;height:114px;border-bottom:2px solid #777}
.rivet{width:8px;height:8px;border-radius:50%;background:radial-gradient(circle at 35% 35%,#fff,#888)}
.brand{left:48px;top:40px;display:flex;align-items:center;gap:8px;font-size:15px;font-weight:600;color:#1f3f7a}
.brand-mark{width:22px;height:22px;background:#1f3f7a}
.phone{left:652px;top:18px;display:flex;align-items:center;gap:6px;font-size:12px;color:var(--blue)}
.phone-icon{width:19px;height:19px;border:1px solid #777;border-radius:50%;display:flex;align-items:center;justify-content:center}
.nav{left:285px;top:70px;display:flex;align-items:center;font-size:9.6px;font-weight:600;color:#333}
.nav a{text-decoration:none;color:inherit;margin-right:21px}
.nav .active{color:var(--blue);padding:8px 12px;margin-right:11px;margin-left:-12px;background:linear-gradient(#f2f2f2,#c8c8c8);box-shadow:0 1px 3px rgba(0,0,0,.45)}
/* hero */
.hero{left:0;top:114px;width:804px;height:323px;background:linear-gradient(180deg,#8a6a3a 0%,#c48a3a 30%,#6a4020 65%,#1a1410 100%)}
.hero-copy{left:495px;top:137px;color:#fff}
.hero-copy h1{font-weight:400;font-size:17px;line-height:16px}
.hero-copy p{font-size:10px;margin-top:4px}
.btn-more{left:495px;top:212px;width:87px;height:26px;font-size:9px;font-weight:600;color:var(--blue);background:linear-gradient(#ededed,#bcbcbc);display:flex;align-items:center;justify-content:center;box-shadow:0 1px 2px rgba(0,0,0,.5)}
.dots{left:361px;top:300px;display:flex;gap:6px}
.dots span{width:23px;height:3px;border-radius:2px;background:#fff}
.dots span:first-child{background:var(--red)}
/* content */
.section-title{width:804px;text-align:center;color:var(--red);font-size:17px;font-weight:400}
.intro{left:94px;top:494px;width:610px;text-align:center;font-size:10.3px;line-height:12px}
.col{width:206px;text-align:center}
.col h3{font-size:17.5px;font-weight:400;height:30px}
.col .photo{width:202px;height:113px;margin:0 auto}
.col p{font-size:10.3px;line-height:12px;margin-top:12px}
.col a{display:block;margin-top:11px;font-size:10.3px;color:var(--red);text-decoration:none}
.testi-title{left:89px;top:848px;font-size:12.5px}
.testi-rule{left:89px;width:264px;height:1px;background:#ccc}
.avatar{left:89px;width:72px}
.t-name{left:171px;font-size:12px}
.t-text{left:171px;width:180px;font-size:9px;line-height:11px}
.quick{left:415px;top:876px;width:322px;height:156px;box-shadow:0 1px 4px rgba(0,0,0,.45)}
.quick h4{position:absolute;left:23px;top:19px;font-size:12px;font-weight:400}
.field{position:absolute;width:134px;height:23px;background:#fff;font-size:9px;color:#888;padding:5px 12px}
.arrow{position:absolute;right:8px;top:9px}
.submit{position:absolute;left:219px;top:113px;width:76px;height:24px;background:linear-gradient(#f4f4f4,#b4b4b4);font-size:11px;display:flex;align-items:center;justify-content:center;box-shadow:0 1px 3px rgba(0,0,0,.5)}
/* footer */
.footer{left:0;top:1064px;width:804px;height:100px}
.f-col{top:13px;font-size:10px;line-height:14.4px}
.f-col h5{font-size:11.5px;font-weight:400;color:#222;margin-bottom:1px}
.f-col .link{color:var(--footer-link)}
.f-col .plain{color:#222}
.social{left:671px;top:18px;display:flex;gap:4px}
.social span{width:20px;height:20px;border-radius:50%;background:#1a1a1a}
.bar{left:0;top:1164px;width:804px;height:36px;background:var(--bar);color:#aaa;font-size:8px}
.bar p{position:absolute;right:70px;top:12px}
</style>
</head>
<body>
<div class="site">
  <header class="abs header metal">
    <span class="abs rivet" style="left:11px;top:11px"></span>
    <span class="abs rivet" style="left:11px;top:95px"></span>
    <span class="abs rivet" style="right:11px;top:11px"></span>
    <span class="abs rivet" style="right:11px;top:95px"></span>
    <div class="abs brand"><span class="brand-mark"></span>Redgum Ridge Towing</div>
    <div class="abs phone">
      <span class="phone-icon"><svg width="11" height="11" viewBox="0 0 24 24"><path d="M6.6 10.8a15 15 0 0 0 6.6 6.6l2.2-2.2c.3-.3.7-.4 1-.2 1.1.4 2.3.6 3.6.6.6 0 1 .4 1 1V20c0 .6-.4 1-1 1A17 17 0 0 1 3 4c0-.6.4-1 1-1h3.5c.6 0 1 .4 1 1 0 1.3.2 2.5.6 3.6.1.3 0 .7-.2 1z" fill="#666"/></svg></span>
      0800 555 0147
    </div>
    <nav class="abs nav">
      <a class="active">HOME</a><a>ABOUT US</a><a>SERVICES</a><a>GALLERY</a><a>BLOG</a><a>TESTIMONIALS</a><a>CONTACT US</a>
    </nav>
  </header>

  <section class="abs hero" role="img" aria-label="Pickup truck towing a trailer along a country road at sunset"></section>
  <div class="abs hero-copy">
    <h1>WE PROVIDE TOWING SERVICE<br>AND CAR BREAKDOWN<br>SERVICEIN AUSTRALIA</h1>
    <p>CLICK HERE TO KNOW MORE DETAILS</p>
  </div>
  <div class="abs btn-more">KNOW MORE</div>
  <div class="abs dots"><span></span><span></span><span></span></div>

  <h2 class="abs section-title" style="top:463px">TOWING SERVICES &amp; CAR BREAK DOWN</h2>
  <p class="abs intro">The Redgum Ridge Company is a forward-thinking company, dedicated to leading the market in portable toilet hire provisions. We aim to exceed our customers expectations by continually evaluating our customers needs and working diligently to provide innovative, effective working solutions. Our committed RRT team remain focused on providing outstanding customer service as always and can be on hand throughout your project or event to ensure you have the help and advice you need, when you need it.</p>

  <h2 class="abs section-title" style="top:564px">OUR SERVICES</h2>
  <div class="abs col" style="left:72px;top:598px">
    <h3>Towing services</h3>
    <div class="photo" role="img" aria-label="Tow truck on a highway beside a lake" style="background:linear-gradient(180deg,#a9bfd6 0%,#6f8a5a 40%,#8a7a5a 70%,#5a5040 100%)"></div>
    <p>With the ability to provide all of your sanitation solutions, a friendly and knowledgeable staff base, competitive pricing...</p>
    <a>Read more</a>
  </div>
  <div class="abs col" style="left:299px;top:598px">
    <h3>Car Breakdown services</h3>
    <div class="photo" role="img" aria-label="Red warning triangle on the road behind a broken-down car" style="background:linear-gradient(180deg,#7a9a5a 0%,#8a9070 40%,#5a5a5a 75%,#4a4a4a 100%)"></div>
    <p>With the ability to provide all of your sanitation solutions, a friendly and knowledgeable staff base, competitive pricing...</p>
    <a>Read more</a>
  </div>
  <div class="abs col" style="left:525px;top:598px">
    <h3>Auto Repair</h3>
    <div class="photo" role="img" aria-label="Mechanic's hands working on a car engine" style="background:linear-gradient(135deg,#2a2a2a 0%,#555 40%,#b08a70 60%,#333 100%)"></div>
    <p>With the ability to provide all of your sanitation solutions, a friendly and knowledgeable staff base, competitive pricing...</p>
    <a>Read more</a>
  </div>

  <h4 class="abs testi-title" style="font-weight:400">TESTIMONIALS</h4>
  <div class="abs testi-rule" style="top:873px"></div>
  <div class="abs avatar" role="img" aria-label="Portrait of a smiling customer" style="top:883px;height:65px;background:linear-gradient(#e8e8e8,#b9a48f)"></div>
  <div class="abs t-name" style="top:885px">Tara Wells</div>
  <p class="abs t-text" style="top:906px">Kestrel Cover Fast efficient polite service again today from your agents the best warranty service I have ever used!!!</p>
  <div class="abs testi-rule" style="top:958px"></div>
  <div class="abs avatar" role="img" aria-label="Portrait of a smiling customer" style="top:966px;height:69px;background:linear-gradient(#d8d0c4,#8a6a50)"></div>
  <div class="abs t-name" style="top:969px">Owen Barker</div>
  <p class="abs t-text" style="top:990px">Kestrel Cover Fast efficient polite service again today from your agents the best warranty service I have ever used!!!</p>

  <form class="abs quick metal">
    <h4>QUICK CONTACT</h4>
    <div class="field" style="left:22px;top:46px">Name</div>
    <div class="field" style="left:160px;top:46px">Phone</div>
    <div class="field" style="left:22px;top:79px">Email</div>
    <div class="field" style="left:160px;top:79px">Service required
      <svg class="arrow" width="8" height="6" viewBox="0 0 8 6"><path d="M0 0h8L4 6z" fill="#c4161c"/></svg>
    </div>
    <div class="submit">SUBMIT</div>
  </form>

  <footer class="abs footer metal">
    <div class="abs f-col" style="left:67px">
      <h5>MENU LINKS</h5>
      <div class="link">About Us</div><div class="link">Services</div><div class="link">Construction</div><div class="link">Contact Us</div>
    </div>
    <div class="abs f-col" style="left:192px">
      <h5>SERVICES</h5>
      <div class="link">Towing</div><div class="link">Roadside Services</div><div class="link">Auto Repair</div><div class="link">Vehicle Storage</div>
    </div>
    <div class="abs f-col" style="left:319px">
      <h5>CONTACT</h5>
      <div class="plain"># 12-48, Sydney</div><div class="plain">Australia</div><div class="plain">HelpLine: 0939 0555 214</div>
    </div>
    <div class="abs social"><span></span><span></span><span></span></div>
  </footer>
  <div class="abs bar"><p>© 2014 REDGUM RIDGE TOWING. ALL RIGHTS ARE RESERVED</p></div>
</div>
</body>
</html>
```